Business card for a new cabinet shop company named Veloran Cabinets for high end cabinets

Design a business card, thinking dark rich green with colours to speak of high end luxury ie; cream, gold, black possibly

Mitchell Tarrowby
Director Craftsman
Email: info@veloranjoinery-example.com.au
Instagram : @veloran.cabinets

```html
<!DOCTYPE html>
<html lang="en">
<head>
<meta charset="utf-8">
<title>Veloran Cabinets – Business Card</title>
<link rel="stylesheet" href="https://fonts.googleapis.com/css2?family=Barlow:wght@400;500;700&display=swap">
<style>
  :root {
    --backdrop: #121413;
    --card: #1c3328;
    --gold: #c9a55a;
    --gold-line: #b8964c;
    --cream: #d9cfb6;
    --shadow: rgba(0, 0, 0, 0.6);
  }
  * { box-sizing: border-box; margin: 0; padding: 0; }
  html, body {
    width: 1200px;
    height: 875px;
    overflow: hidden;
    background: var(--backdrop);
    font-family: "Barlow", Arial, sans-serif;
  }
  .canvas {
    width: 1200px;
    height: 875px;
    display: flex;
    align-items: center;
    justify-content: center;
    gap: 44px;
  }
  .card {
    position: relative;
    width: 520px;
    height: 300px;
    background: var(--card);
    border-radius: 16px;
    border-bottom: 1.5px solid var(--gold-line);
    border-right: 1.5px solid var(--gold-line);
    box-shadow: 0 24px 50px var(--shadow);
  }

  /* Front */
  .card-front {
    display: flex;
    align-items: center;
    justify-content: center;
    gap: 18px;
  }
  .brand-square {
    width: 34px;
    height: 34px;
    border: 2px solid var(--gold);
  }
  .brand-name {
    font-weight: 500;
    font-size: 40px;
    letter-spacing: 1px;
    color: var(--gold);
    white-space: nowrap;
  }

  /* Back */
  .brand-small {
    position: absolute;
    top: 30px;
    right: 34px;
    font-weight: 500;
    font-size: 14px;
    letter-spacing: 0.5px;
    color: var(--gold);
  }
  .details {
    position: absolute;
    left: 20px;
    right: 20px;
    top: 118px;
    display: flex;
    align-items: center;
    justify-content: center;
  }
  .person {
    text-align: right;
    padding-right: 14px;
    white-space: nowrap;
  }
  .person-name {
    font-weight: 700;
    font-size: 21px;
    color: var(--gold);
    text-transform: uppercase;
    letter-spacing: 0.3px;
    line-height: 1.15;
  }
  .person-role {
    font-size: 14px;
    color: var(--cream);
    margin-top: 2px;
  }
  .divider {
    width: 1.5px;
    height: 62px;
    background: var(--gold);
    flex: none;
  }
  .contact-list {
    list-style: none;
    padding-left: 12px;
  }
  .contact-item {
    display: flex;
    align-items: center;
    gap: 7px;
    font-size: 12px;
    color: var(--cream);
    line-height: 20px;
    white-space: nowrap;
  }
  .contact-icon {
    width: 11px;
    height: 11px;
    flex: none;
  }
</style>
</head>
<body>
<main class="canvas">
  <section class="card card-front">
    <span class="brand-square"></span>
    <span class="brand-name">Veloran Cabinets</span>
  </section>

  <section class="card card-back">
    <span class="brand-small">Veloran Cabinets</span>
    <div class="details">
      <div class="person">
        <p class="person-name">Mitchell Tarrowby</p>
        <p class="person-role">Director Craftsman</p>
      </div>
      <span class="divider"></span>
      <ul class="contact-list">
        <li class="contact-item">
          <svg class="contact-icon" viewBox="0 0 12 12" aria-hidden="true"><path d="M2.5 1 L4.5 1 L5 3.5 L3.8 4.4 Q4.8 6.8 7.6 8.2 L8.5 7 L11 7.5 L11 9.5 Q11 11 9.5 11 Q1 10 1 2.5 Q1 1 2.5 1 Z" fill="var(--gold)"/></svg>
          555.010.2468
        </li>
        <li class="contact-item">
          <svg class="contact-icon" viewBox="0 0 12 12" aria-hidden="true"><rect x="0.5" y="2" width="11" height="8" fill="var(--gold)"/><path d="M0.8 2.3 L6 6.5 L11.2 2.3" fill="none" stroke="var(--card)" stroke-width="1"/></svg>
          info@veloranjoinery-example.com.au
        </li>
        <li class="contact-item">
          <svg class="contact-icon" viewBox="0 0 12 12" aria-hidden="true"><circle cx="6" cy="6" r="4.6" fill="none" stroke="var(--gold)" stroke-width="1.4"/></svg>
          @veloran.cabinets
        </li>
      </ul>
    </div>
  </section>
</main>
</body>
</html>
```